Publishing House

Amber Heron
Exotic, they weave silk out of nowhere. Blessed with a keen sense. Sophisticated discernment. Fearsome reputation. Powerful, but do not harm. Unless, you really needle them. Believe in continuous improvement. A young tarantula may shed its exoskeleton periodically in order to grow, a process called molting : several times a year as a part of the maturation process.
White. The colour pristine. Everything pure. Blemish-free. We feel for the writer. We want to infuse spurt of purity into publishing.
We, at Amber Heron Publishing, are here to question the status-quo, to provide a fresh, invigorating platform for writers to reach their art to their readership via processes that are transparent, impartial and non-discriminatory, and a level of transparency that will set new benchmarks in the world of publishing.
We bring to you new concepts in the areas of editing, proof-reading and cover-designing. Our suite of marketing services targets new, and web-based methods as well as traditional methods.
It is time the writer got his or her due!

I have attached our logo also

Industry/Entity Type

House

```html
<!DOCTYPE html>
<html lang="en">
<head>
<meta charset="utf-8">
<title>Amber Heron Publishing – Cover</title>
<link rel="stylesheet" href="https://fonts.googleapis.com/css2?family=Russo+One&family=Cinzel:wght@400;700&display=swap">
<style>
  :root {
    --page-bg: #e9ebee;
    --shelf-dark: #2a1d14;
    --wood: #8a5a2b;
    --wood-light: #b7834a;
    --spine-blue: #2f4f7a;
    --spine-red: #8e2a2a;
    --spine-cream: #d8cdb4;
    --plaque: #c79a5c;
    --plaque-dark: #8f6434;
    --plaque-ink: #4a2f17;
    --headline: #f6b418;
    --subline: #ffffff;
    --band: rgba(30, 20, 12, 0.78);
    --avatar-bg: #1f1b1c;
    --avatar-frame: #ffffff;
    --avatar-edge: #b9bcc2;
    --gold: #d2ad5c;
  }
  * { margin: 0; padding: 0; box-sizing: border-box; }
  html, body { width: 1200px; height: 718px; overflow: hidden; background: var(--page-bg); }
  .canvas { position: relative; width: 1200px; height: 718px; }

  .cover {
    position: absolute; left: 40px; top: 100px; width: 1120px; height: 413px; overflow: hidden;
  }
  .cover__photo {
    position: absolute; inset: 0;
    background:
      linear-gradient(90deg, rgba(47,79,122,.55), rgba(142,42,42,.45) 25%, rgba(216,205,180,.35) 45%, rgba(47,79,122,.5) 65%, rgba(142,42,42,.4) 85%, rgba(216,205,180,.35)),
      linear-gradient(180deg, var(--shelf-dark) 0%, #3c2c20 18%, var(--wood-light) 22%, var(--wood) 36%, #5a3a1d 42%, var(--shelf-dark) 47%, #3a2e28 60%, var(--spine-cream) 78%, #4b3a30 100%);
  }
  .cover__band {
    position: absolute; left: 430px; right: 0; top: 172px; height: 98px;
    background: linear-gradient(90deg, rgba(30,20,12,0) 0%, var(--band) 25%, var(--band) 100%);
  }
  .cover__headline {
    position: absolute; right: 16px; top: 180px;
    font-family: "Russo One", sans-serif; font-size: 29px; color: var(--headline);
    letter-spacing: .5px; white-space: nowrap;
  }
  .cover__subline {
    position: absolute; right: 36px; top: 226px;
    font-family: "Russo One", sans-serif; font-size: 24px; color: var(--subline);
    letter-spacing: 1px; white-space: nowrap;
  }

  .plaque {
    position: absolute; left: 840px; top: 63px; width: 258px; height: 76px;
    background: linear-gradient(180deg, var(--plaque) 0%, #b8874c 60%, var(--plaque-dark) 100%);
    border: 2px solid #6e4823; border-radius: 4px;
    box-shadow: 0 3px 6px rgba(0,0,0,.45);
    text-align: center; color: var(--plaque-ink);
  }
  .plaque__nail {
    position: absolute; top: 7px; width: 7px; height: 7px; border-radius: 50%; background: #5a3a1d;
  }
  .plaque__nail--left { left: 8px; }
  .plaque__nail--right { right: 8px; }
  .plaque__label {
    font-family: "Cinzel", serif; font-size: 19px; letter-spacing: 1px; margin-top: 8px;
  }
  .plaque__phone {
    font-family: "Cinzel", serif; font-weight: 700; font-size: 22px; color: #fff4df; letter-spacing: 1px; margin-top: 2px;
  }

  .avatar {
    position: absolute; left: 72px; top: 357px; width: 220px; height: 222px;
    background: var(--avatar-frame); border: 1px solid var(--avatar-edge);
    padding: 6px; box-shadow: 0 1px 3px rgba(0,0,0,.25);
  }
  .avatar__inner {
    width: 100%; height: 100%; background: var(--avatar-bg);
    display: flex; align-items: center; justify-content: center;
  }
  .avatar__name {
    font-family: "Russo One", sans-serif; font-size: 24px; color: var(--gold); letter-spacing: .5px;
  }
</style>
</head>
<body>
<main class="canvas">
  <section class="cover">
    <div class="cover__photo" role="img" aria-label="Photograph of two wooden shelves filled with colourful book spines"></div>
    <div class="cover__band"></div>
    <div class="plaque">
      <span class="plaque__nail plaque__nail--left"></span>
      <span class="plaque__nail plaque__nail--right"></span>
      <p class="plaque__label">CALL US TODAY</p>
      <p class="plaque__phone">+91 5550 1234 00</p>
    </div>
    <h1 class="cover__headline">WRITERS, BOOK READERS ARE WELCOME !</h1>
    <p class="cover__subline">ONE PLACE FOR ALL YOUR SOLUTIONS</p>
  </section>

  <div class="avatar">
    <div class="avatar__inner">
      <span class="avatar__name">Amber Heron</span>
    </div>
  </div>
</main>
</body>
</html>
```